RM Tomás Ledesma (Business Card)

Hi designers, in this work, I'm looking for an sophisticated stylish, elegant and proffesional personal card. We have a laboratory of pathology automated, with equipments high quality.
In this web the designers, have created my business logo, the name is "RM Tomás Ledesma"
In our lab, we principal work is to prepare the biopsies for further diagnostic of diseases like cancer, tumors, etc.
I need that the first face, only having my complete logo (Rm Tomás Ledesma, Laboratorio de procesamiento Histologico)
The overleaf, could repeat the same logo, like water logo.
In this face, I need to say: My full data:

Técnico en Anatomía Patológica
Tomás Ledesma Urquiza M.P 48213
Av. Duarte Quirós 817 - 2do piso - Instituto Brandsen.
Córdoba, Argentina
(0351) 158246093
ledesma.tomas@correoviva.com.ar

with respect the colors of card, use your imagination, the original logo color is violet, I haven't chosen a color base for the card.

attached pictures are examples of cards I like your DESIGN.
Attached too, the original logo to my company.

the size of card are:
horizontal: 9cm
vertical: 5,5cm

any question that you have, not doubt to question me,
Hand to work!

Industry/Entity Type

Laboratory

Requirements
Must have
• designers sophisticated, not simples, like show the images attached

```html
<!DOCTYPE html>
<html lang="es">
<head>
<meta charset="utf-8">
<title>RM Tomás Ledesma – Papelería</title>
<link rel="stylesheet" href="https://fonts.googleapis.com/css2?family=Oswald:wght@400&family=Raleway:wght@300;400&display=swap">
<style>
  :root{
    --backdrop:#3a3634;
    --paper:#f4f4f5;
    --paper-shade:#e6e6e8;
    --violet:#4a2470;
    --violet-dark:#2f1250;
    --swoosh:#c9c9cd;
    --ink:#6b6b70;
    --ink-light:#9a9aa0;
    --white:#ffffff;
  }
  *{box-sizing:border-box;margin:0;padding:0}
  html,body{width:1200px;height:900px;overflow:hidden;background:var(--backdrop)}
  .canvas{position:relative;width:1200px;height:900px}
  .sheet{position:absolute;overflow:hidden;background:linear-gradient(160deg,var(--white),var(--paper) 55%,var(--paper-shade));box-shadow:0 6px 18px rgba(0,0,0,.45)}
  .wave{position:absolute;left:0;bottom:0;width:100%;display:block}

  .brand{position:absolute;display:flex;flex-direction:column;align-items:flex-start}
  .brand-row{display:flex;align-items:center;gap:6px}
  .brand-dot{border-radius:50%;border:2px solid var(--violet);flex:none}
  .brand-name{font-family:"Oswald",sans-serif;font-weight:400;color:var(--violet);letter-spacing:.12em;text-transform:uppercase;white-space:nowrap}
  .brand-tagline{font-family:"Oswald",sans-serif;font-weight:400;color:var(--ink);text-transform:uppercase;white-space:nowrap;border-top:1px solid var(--ink-light);margin-top:3px;padding-top:2px}

  .faint-mark{position:absolute;font-family:"Oswald",sans-serif;font-weight:400;color:rgba(120,120,130,.09);text-transform:uppercase;letter-spacing:.1em;white-space:nowrap}

  .contact{position:absolute;font-family:"Raleway",sans-serif;font-weight:300;color:var(--ink);line-height:1.5;white-space:nowrap}
  .contact-line{display:flex;align-items:center;gap:6px}
  .icon{flex:none;fill:currentColor}
  .on-violet{color:var(--white)}

  /* letterhead */
  .letterhead{left:70px;top:80px;width:460px;height:660px}
  .letterhead .brand{left:70px;top:60px}
  .letterhead .brand-dot{width:22px;height:22px}
  .letterhead .brand-name{font-size:13px}
  .letterhead .brand-tagline{font-size:10px}
  .letterhead .faint-mark{left:50%;top:300px;transform:translateX(-50%);font-size:34px}
  .letterhead .contact{font-size:10px}
  .letterhead .address{right:30px;top:505px;text-align:right}
  .letterhead .reach{left:200px;top:540px}

  /* large card */
  .card-large{left:580px;top:110px;width:460px;height:260px}
  .card-large .brand{left:30px;top:26px}
  .card-large .brand-dot{width:14px;height:14px;border-width:1.5px}
  .card-large .brand-name{font-size:9px}
  .card-large .brand-tagline{font-size:7px}
  .card-large .faint-mark{left:190px;top:80px;font-size:22px}
  .card-large .contact{font-size:8.5px}
  .card-large .address{right:10px;top:118px;text-align:right}
  .card-large .reach{left:26px;top:218px}

  /* small cards */
  .card-small{width:330px;height:200px;border-radius:10px}
  .card-front{left:700px;top:430px}
  .card-back{left:700px;top:660px}
  .card-front .brand{left:50%;top:52px;transform:translateX(-50%);align-items:center}
  .card-front .brand-dot{width:18px;height:18px}
  .card-front .brand-name{font-size:12px}
  .card-front .brand-tagline{font-size:9px}
  .card-back .brand{left:50%;top:20px;transform:translateX(-50%);align-items:center}
  .card-back .brand-dot{width:12px;height:12px;border-width:1.5px}
  .card-back .brand-name{font-size:8px}
  .card-back .brand-tagline{font-size:6px}
  .card-back .contact{font-size:7px}
  .card-back .address{left:50%;top:62px;transform:translateX(-50%);text-align:center;font-size:6px}
  .card-back .holder{left:24px;top:98px}
  .card-back .reach{left:188px;top:102px}
  .holder-name{font-family:"Raleway",sans-serif;font-weight:400;font-size:10px;color:var(--ink)}
  .divider{position:absolute;left:178px;top:96px;width:1px;height:46px;background:var(--ink-light)}
</style>
</head>
<body>
<main class="canvas">

  <section class="sheet letterhead">
    <div class="brand">
      <div class="brand-row"><span class="brand-dot"></span><span class="brand-name">RM Tomás Ledesma</span></div>
      <span class="brand-tagline">Laboratorio de procesamiento histologico</span>
    </div>
    <span class="faint-mark">RM Tomás Ledesma</span>
    <div class="contact address">
      <div>Av. Duarte Quirós 817 - 2do piso - Instituto</div>
      <div>Brandsen, Córdoba, Argentina</div>
    </div>
    <div class="contact reach">
      <div class="contact-line"><svg class="icon" width="8" height="10" viewBox="0 0 8 10"><rect x="1" y="0" width="6" height="10" rx="1"/></svg>(0351) 158246093</div>
      <div class="contact-line"><svg class="icon" width="10" height="8" viewBox="0 0 10 8"><rect width="10" height="8" rx="1"/></svg>ledesma.tomas@correoviva.com.ar</div>
    </div>
    <svg class="wave" viewBox="0 0 460 130" height="130" preserveAspectRatio="none" aria-hidden="true">
      <path d="M0,40 Q200,90 460,20 L460,130 L0,130Z" fill="var(--swoosh)"/>
      <path d="M0,52 Q200,98 460,32 L460,130 L0,130Z" fill="var(--white)"/>
      <path d="M0,62 Q200,104 460,44 L460,130 L0,130Z" fill="var(--violet)"/>
    </svg>
  </section>

  <section class="sheet card-large">
    <div class="brand">
      <div class="brand-row"><span class="brand-dot"></span><span class="brand-name">RM Tomás Ledesma</span></div>
      <span class="brand-tagline">Laboratorio de procesamiento histologico</span>
    </div>
    <span class="faint-mark">RM Tomás Ledesma</span>
    <svg class="wave" viewBox="0 0 460 150" height="150" preserveAspectRatio="none" aria-hidden="true">
      <path d="M0,80 Q240,95 460,10 L460,150 L0,150Z" fill="var(--swoosh)"/>
      <path d="M0,92 Q240,104 460,24 L460,150 L0,150Z" fill="var(--white)"/>
      <path d="M0,100 Q240,110 460,36 L460,150 L0,150Z" fill="var(--violet)"/>
    </svg>
    <div class="contact address">
      <div>Av. Duarte Quirós 817 - 2do piso - Instituto</div>
      <div>Brandsen, Córdoba, Argentina</div>
    </div>
    <div class="contact on-violet reach">
      <div class="contact-line"><svg class="icon" width="7" height="9" viewBox="0 0 8 10"><rect x="1" y="0" width="6" height="10" rx="1"/></svg>(0351) 158246093</div>
      <div class="contact-line"><svg class="icon" width="9" height="7" viewBox="0 0 10 8"><rect width="10" height="8" rx="1"/></svg>ledesma.tomas@correoviva.com.ar</div>
    </div>
  </section>

  <section class="sheet card-small card-front">
    <div class="brand">
      <div class="brand-row"><span class="brand-dot"></span><span class="brand-name">RM Tomás Ledesma</span></div>
      <span class="brand-tagline">Laboratorio de procesamiento histologico</span>
    </div>
    <svg class="wave" viewBox="0 0 330 90" height="90" preserveAspectRatio="none" aria-hidden="true">
      <path d="M0,40 Q170,20 330,10 L330,90 L0,90Z" fill="var(--swoosh)"/>
      <path d="M0,50 Q170,30 330,22 L330,90 L0,90Z" fill="var(--white)"/>
      <path d="M0,58 Q170,38 330,32 L330,90 L0,90Z" fill="var(--violet)"/>
    </svg>
  </section>

  <section class="sheet card-small card-back">
    <div class="brand">
      <div class="brand-row"><span class="brand-dot"></span><span class="brand-name">RM Tomás Ledesma</span></div>
      <span class="brand-tagline">Laboratorio de procesamiento histologico</span>
    </div>
    <div class="contact address">
      <div>Av. Duarte Quirós 817 - 2do piso - Instituto Brandsen</div>
      <div>Córdoba, Argentina</div>
    </div>
    <div class="contact holder">
      <div class="holder-name">Tomás Ledesma Urquiza</div>
      <div>Técnico en Anatomía Patológica</div>
      <div>M.P 48213</div>
    </div>
    <span class="divider"></span>
    <div class="contact reach">
      <div class="contact-line"><svg class="icon" width="6" height="8" viewBox="0 0 8 10"><rect x="1" y="0" width="6" height="10" rx="1"/></svg>(0351) 158246093</div>
      <div class="contact-line"><svg class="icon" width="8" height="6" viewBox="0 0 10 8"><rect width="10" height="8" rx="1"/></svg>ledesma.tomas@correoviva.com.ar</div>
    </div>
    <svg class="wave" viewBox="0 0 330 40" height="40" preserveAspectRatio="none" aria-hidden="true">
      <path d="M0,8 Q165,28 330,4 L330,40 L0,40Z" fill="var(--swoosh)"/>
      <path d="M0,14 Q165,32 330,10 L330,40 L0,40Z" fill="var(--white)"/>
      <path d="M0,20 Q165,36 330,16 L330,40 L0,40Z" fill="var(--violet)"/>
    </svg>
  </section>

</main>
</body>
</html>
```